Business Card Design for Occupational Medicine Start Up Company

We need to design a professional business card. We are a healthcare company providing occupational medicine services to blue collar industries. We are professional, efficient and high quality service providers.

Target Market(s)

Blue Collar Industry: Shipbuilding, Ports, Trucking Companies; The Executives and Safety Officers for these companies

Industry/Entity Type

Healthcare

Contact Information for Business Card

Logo, Name, Title, Email, Phone

Other font styles liked:
• Please match our Brand Guide

Requirements
Must have
• Our Company Colors and Logo

```html
<!DOCTYPE html>
<html lang="en">
<head>
<meta charset="utf-8">
<title>CrewWell Business Card</title>
<link href="https://fonts.googleapis.com/css2?family=Montserrat:wght@700&family=Roboto:wght@400;700&display=swap" rel="stylesheet">
<style>
  :root {
    --navy: #2a3587;
    --navy-deep: #222c78;
    --navy-soft: #3341a0;
    --gold: #f3ad3c;
    --white: #ffffff;
    --stage: #e9eaee;
  }
  * { margin: 0; padding: 0; box-sizing: border-box; }
  html, body { width: 1200px; height: 912px; overflow: hidden; }
  body {
    background: var(--stage);
    position: relative;
    font-family: "Roboto", Arial, sans-serif;
  }
  .card {
    position: absolute;
    top: 296px;
    width: 560px;
    height: 320px;
    overflow: hidden;
    box-shadow: 0 6px 18px rgba(0,0,0,0.18);
  }
  .card--back { left: 27px; background: var(--navy); }
  .card--front { left: 613px; background: var(--white); }

  .back-pattern {
    position: absolute; inset: 0;
    background: radial-gradient(ellipse at 60% 40%, var(--navy-soft), var(--navy-deep) 75%);
  }
  .back-brand {
    position: absolute;
    left: 0; right: 0; top: 138px;
    display: flex; align-items: center; justify-content: center; gap: 12px;
  }
  .brand-dot {
    width: 30px; height: 30px; border-radius: 50%;
    background: var(--white);
  }
  .brand-name {
    font-family: "Montserrat", Arial, sans-serif;
    font-weight: 700;
    font-size: 38px;
    letter-spacing: 1px;
    color: var(--white);
    line-height: 1.1;
  }

  .front-band { position: absolute; inset: 0; }
  .front-brand {
    position: absolute;
    left: 0; right: 0; top: 36px;
    display: flex; flex-direction: column; align-items: center; gap: 8px;
  }
  .front-brand .brand-dot { width: 46px; height: 46px; background: var(--navy); }
  .front-brand .brand-name { color: var(--navy); font-size: 38px; }

  .holder {
    position: absolute;
    right: 34px; top: 192px;
    text-align: right;
  }
  .holder__name {
    font-weight: 700; font-size: 22px;
    color: var(--gold); letter-spacing: 0.3px;
  }
  .holder__title {
    font-size: 13px; color: var(--white); margin-top: 2px;
  }

  .contact {
    position: absolute;
    left: 26px; bottom: 18px;
    list-style: none;
    color: var(--white);
    font-size: 13.5px;
    line-height: 19px;
  }
  .contact li { display: flex; align-items: center; gap: 6px; }
  .contact svg { width: 12px; height: 12px; flex: none; }
</style>
</head>
<body>

  <section class="card card--back" aria-label="Card back">
    <div class="back-pattern" role="img" aria-label="Embossed repeating brand pattern in deep blue"></div>
    <div class="back-brand">
      <span class="brand-dot"></span>
      <span class="brand-name">CREWWELL</span>
    </div>
  </section>

  <section class="card card--front" aria-label="Card front">
    <svg class="front-band" viewBox="0 0 560 320" width="560" height="320" aria-hidden="true">
      <polygon points="0,232 374,168 386,181 398,165 560,134 560,320 0,320" fill="var(--navy)"/>
      <polyline points="0,222 372,158 386,172 400,155 560,124" fill="none" stroke="var(--gold)" stroke-width="3"/>
    </svg>

    <div class="front-brand">
      <span class="brand-dot"></span>
      <span class="brand-name">CREWWELL</span>
    </div>

    <div class="holder">
      <div class="holder__name">MARK ELLISON</div>
      <div class="holder__title">Director</div>
    </div>

    <ul class="contact">
      <li>
        <svg viewBox="0 0 12 12"><path d="M2.5 1 L4.5 1 L5.2 3.6 L4 4.6 C4.7 6 5.9 7.3 7.4 8 L8.4 6.8 L11 7.5 L11 9.5 C11 10.4 10.3 11 9.5 11 C5 10.6 1.4 7 1 2.5 C1 1.7 1.6 1 2.5 1 Z" fill="var(--gold)"/></svg>
        (480) 555 0142
      </li>
      <li>
        <svg viewBox="0 0 12 12"><rect x="0.5" y="2" width="11" height="8" fill="var(--gold)"/><polyline points="0.8,2.3 6,6.6 11.2,2.3" fill="none" stroke="var(--navy)" stroke-width="1"/></svg>
        hello@crewwell.com
      </li>
      <li>
        <svg viewBox="0 0 12 12"><circle cx="6" cy="6" r="5.3" fill="var(--gold)"/><g fill="none" stroke="var(--navy)" stroke-width="0.8"><ellipse cx="6" cy="6" rx="2.3" ry="5.3"/><line x1="0.7" y1="6" x2="11.3" y2="6"/><line x1="6" y1="0.7" x2="6" y2="11.3"/></g></svg>
        www.crewwell.com
      </li>
    </ul>
  </section>

</body>
</html>
```